Harrow Point Metrics Company Website Design and Coding

We want to redesign our existing website so that it is more visually and functionally appealing to prospective clients and potential job candidates. We would like to keep our current color scheme and implement our current logo as well. We have a high-level idea of website structure that we are thinking of, which is in the attached files. Logo is included as well. The final design would ideally be energy and analytics focused. We will need the new website to be coded as well, please.

Target Market(s)

Energy and utility industry

Industry/Entity Type

Energy/analytics

Coding

Coded - Design and coding required

Number of Pages Required

5+ page

Font styles to use
Sans Serif

Colors
0094D4
00A9DD
6FCCEA
C7EBF8
E9F6FB
F0912C
F2A743
F7CA91
FBE8D2
FDF5EE

Requirements
Must have
• Consistent color scheme- please use the one that we provided. We need an overview, a home page, and our core services. A separate job application page. Logo must be incorporated. We would like e "Meet our Team" page. Please include all of the content that is listed in our attachments.
Nice to have
• Movement
Should not have
• No music, no cartoons/animation, no pictures of a chalkboard

```html
<!DOCTYPE html>
<html lang="en">
<head>
<meta charset="utf-8">
<title>Harrow Point Metrics</title>
<link rel="stylesheet" href="https://fonts.googleapis.com/css2?family=Poppins:ital,wght@0,400;0,500;0,600;0,700;1,400&family=Montserrat:wght@700;800&display=swap">
<style>
:root{
  --blue:#0094D4;
  --blue-2:#00A9DD;
  --blue-3:#6FCCEA;
  --blue-4:#C7EBF8;
  --blue-5:#E9F6FB;
  --orange:#F0912C;
  --orange-2:#F2A743;
  --peach:#F7CA91;
  --peach-2:#FBE8D2;
  --cream:#FDF5EE;
  --ink:#222831;
  --text:#3b3f45;
  --white:#ffffff;
}
*{box-sizing:border-box;margin:0;padding:0}
html,body{width:1200px;height:4136px;overflow:hidden}
body{font-family:'Poppins',sans-serif;color:var(--text);background:var(--white);position:relative}
section,header,footer{position:absolute;left:0;width:1200px}
.btn{position:absolute;background:var(--orange);color:var(--white);font-weight:700;font-size:16px;border-radius:24px;display:flex;align-items:center;justify-content:center}
.heading{font-family:'Montserrat',sans-serif;font-weight:800;color:var(--ink)}

/* header */
.site-header{top:0;height:96px;background:var(--white)}
.brand{position:absolute;display:flex;align-items:center;gap:10px}
.brand-dot{width:30px;height:30px;border-radius:50%;background:var(--blue-3)}
.brand-name{font-family:'Poppins',sans-serif;font-weight:500;color:var(--blue);font-size:24px;white-space:nowrap}
.nav{position:absolute;top:26px;left:477px;display:flex;align-items:center;height:46px}
.nav a{font-size:15px;color:var(--ink);text-decoration:none;margin-right:38px}
.nav a.active{background:var(--orange);color:var(--white);font-weight:600;padding:0 24px;height:46px;display:flex;align-items:center;border-radius:23px;margin-right:32px}

/* hero */
.hero{top:96px;height:672px;background:linear-gradient(120deg,#5a6673 0%,#7d8a98 35%,#9aa6b3 55%,#4b5866 100%)}
.hero::after{content:"";position:absolute;inset:0;background:rgba(20,30,45,.35)}
.hero-inner{position:absolute;inset:0;z-index:1;text-align:center;color:var(--white)}
.hero h1{position:absolute;top:222px;width:100%;font-family:'Montserrat',sans-serif;font-weight:800;font-size:62px;line-height:72px;letter-spacing:1px}
.hero p{position:absolute;top:366px;left:170px;width:860px;font-size:18px;line-height:29px;font-weight:500}
.hero .btn{top:444px;left:525px;width:150px;height:48px}

/* mission */
.mission{top:768px;height:257px;background:var(--blue-5)}
.mission h2{position:absolute;left:83px;top:98px;font-size:52px;line-height:60px}
.mission blockquote{position:absolute;left:433px;top:70px;width:700px;font-style:italic;color:var(--blue);font-size:20px;line-height:39px}

/* services */
.services{top:1025px;height:817px;background:var(--white)}
.services h2{position:absolute;top:70px;width:100%;text-align:center;font-size:46px}
.svc{position:absolute;width:360px;text-align:center}
.svc svg{display:block;margin:0 auto}
.svc h3{font-weight:500;font-size:21px;line-height:34px;color:var(--ink);margin-top:14px}
.vdiv{position:absolute;width:2px;background:linear-gradient(to bottom,rgba(0,0,0,0),rgba(0,0,0,.08),rgba(0,0,0,0))}
.hdiv{position:absolute;height:2px;left:100px;width:1000px;top:463px;background:linear-gradient(to right,rgba(0,0,0,0),rgba(0,0,0,.08),rgba(0,0,0,0))}

/* overview */
.overview{top:1842px;height:587px;background:var(--blue)}
.overview .backing{position:absolute;left:470px;top:93px;width:117px;height:405px;background:var(--blue-3);border-radius:0 30px 30px 0}
.photo{position:absolute}
.overview .photo{left:0;top:60px;width:533px;height:468px;border-radius:0 36px 36px 0;background:linear-gradient(135deg,#c9cfd6 0%,#6d8dad 45%,#2f5f8f 100%)}
.overview h2{position:absolute;left:616px;top:92px;color:var(--white);font-size:46px}
.overview p{position:absolute;left:616px;top:160px;width:500px;color:var(--white);font-size:15px;line-height:31.5px}
.overview .btn{left:616px;top:437px;width:150px;height:46px}

/* case studies */
.cases{top:2429px;height:711px;background:var(--white)}
.cases .frame{position:absolute;left:76px;top:68px;width:628px;height:476px;border:4px solid var(--blue);border-radius:44px}
.cases h2{position:absolute;left:108px;top:110px;z-index:2;font-family:'Poppins',sans-serif;font-weight:600;font-size:42px;line-height:48px;white-space:nowrap}
.checklist{position:absolute;left:108px;top:232px;width:480px;list-style:none}
.checklist li{position:relative;padding-left:34px;font-size:16px;line-height:25px;margin-bottom:17px;color:var(--ink)}
.checklist li::before{content:"";position:absolute;left:0;top:5px;width:16px;height:16px;border-radius:50%;background:var(--blue)}
.checklist li::after{content:"";position:absolute;left:5px;top:8px;width:4px;height:7px;border:solid var(--white);border-width:0 2px 2px 0;transform:rotate(45deg)}
.cases .backing{position:absolute;left:640px;top:146px;width:500px;height:475px;background:var(--peach-2);border-radius:40px}
.cases .photo{left:616px;top:166px;width:510px;height:465px;border-radius:0 40px 40px 40px;background:linear-gradient(135deg,#1d3f6e 0%,#2b65a5 50%,#8fb8e0 100%)}

/* research */
.research{top:3140px;height:707px;background:var(--blue-5)}
.research h2{position:absolute;top:52px;width:100%;text-align:center;font-size:44px}
.card{position:absolute;top:133px;width:329px}
.card .photo{position:relative;width:329px;height:220px;border-radius:16px}
.card h3{margin-top:36px;color:var(--blue);font-family:'Montserrat',sans-serif;font-weight:800;font-size:26px;line-height:30px}
.card p{margin-top:10px;font-size:15px;line-height:29px;color:var(--ink)}
.card a{display:inline-block;margin-top:12px;color:var(--orange);font-weight:700;font-size:14px;text-decoration:underline}
.arrow{position:absolute;top:333px}
.research .btn{left:480px;top:600px;width:240px;height:48px}

/* footer */
.site-footer{top:3847px;height:289px;background:var(--white)}
.site-footer .brand{left:75px;top:95px}
.site-footer .brand-name{font-size:20px}
.site-footer .brand-dot{width:26px;height:26px}
.copyright{position:absolute;left:75px;top:174px;font-size:13px;line-height:25px;color:var(--ink)}
.foot-head{position:absolute;top:65px;color:var(--blue);font-weight:700;font-size:17px}
.foot-links{position:absolute;font-size:14px;color:var(--ink);line-height:37px}
.contact{position:absolute;left:650px;top:100px;font-size:14px;line-height:25px;color:var(--ink)}
.contact .co{color:var(--orange);font-weight:700}
.contact .row{display:flex;align-items:center;gap:14px;margin-top:8px}
.social{position:absolute;left:946px;top:100px;display:flex;gap:21px}
.social span{width:22px;height:22px;background:var(--orange);border-radius:4px}
</style>
</head>
<body>

<header class="site-header">
  <div class="brand" style="left:72px;top:30px"><span class="brand-dot"></span><span class="brand-name">Harrow Point Metrics</span></div>
  <nav class="nav">
    <a class="active" href="#">Home</a>
    <a href="#">About Us</a>
    <a href="#">Core Services</a>
    <a href="#">Our Work</a>
    <a href="#">Blog</a>
    <a href="#">Contact Us</a>
  </nav>
</header>

<section class="hero" role="img" aria-label="Analysts in an office reviewing an energy dashboard on a laptop">
  <div class="hero-inner">
    <h1>LOAD RESEARCH AND<br>FORECASTING</h1>
    <p>Understanding end-use and premise load characteristics is a critical component of system planning, rate design, and time-differentiated energy savings.</p>
    <a class="btn">Read More</a>
  </div>
</section>

<section class="mission">
  <h2 class="heading">Our Mission</h2>
  <blockquote>“ Harrow Point Metrics is a consulting company that helps utilities and regulatory agencies navigate the challenges of building a smarter and cleaner energy future...”</blockquote>
</section>

<section class="services">
  <h2 class="heading">Our Services</h2>
  <div class="vdiv" style="left:419px;top:170px;height:590px"></div>
  <div class="vdiv" style="left:779px;top:170px;height:590px"></div>
  <div class="hdiv"></div>

  <div class="svc" style="left:60px;top:200px">
    <svg width="124" height="124" viewBox="0 0 124 124" fill="none" stroke="#0094D4" stroke-width="4" stroke-linejoin="round">
      <circle cx="70" cy="60" r="42" fill="#FBE8D2" stroke="none"/>
      <rect x="6" y="28" width="112" height="70" rx="4"/>
      <line x1="62" y1="98" x2="62" y2="112"/><line x1="44" y1="114" x2="80" y2="114"/>
      <rect x="20" y="50" width="10" height="30"/><rect x="36" y="40" width="10" height="40"/><rect x="52" y="32" width="10" height="48"/><rect x="68" y="44" width="10" height="36"/>
      <polyline points="14,84 40,66 62,78 96,52"/>
      <circle cx="100" cy="24" r="14" fill="#fff"/><path d="M100 24V10M100 24l12 6"/>
    </svg>
    <h3>Predictive Analytics and<br>Forecasting</h3>
  </div>
  <div class="svc" style="left:420px;top:200px">
    <svg width="124" height="124" viewBox="0 0 124 124" fill="none" stroke="#0094D4" stroke-width="4" stroke-linejoin="round">
      <circle cx="74" cy="60" r="42" fill="#FBE8D2" stroke="none"/>
      <rect x="16" y="14" width="76" height="104" rx="5" fill="#fff"/>
      <rect x="38" y="6" width="32" height="16" rx="4" fill="#fff"/>
      <path d="M28 42l5 5 9-9M28 66l5 5 9-9M28 90l5 5 9-9"/>
      <line x1="50" y1="44" x2="78" y2="44"/><line x1="50" y1="68" x2="74" y2="68"/><line x1="50" y1="92" x2="66" y2="92"/>
      <path d="M106 40l10 10-40 46-14 4 4-14z" fill="#fff"/>
    </svg>
    <h3>T&amp;D<br>Planning</h3>
  </div>
  <div class="svc" style="left:780px;top:200px">
    <svg width="124" height="124" viewBox="0 0 124 124" fill="none" stroke="#0094D4" stroke-width="4" stroke-linejoin="round">
      <circle cx="48" cy="62" r="42" fill="#FBE8D2" stroke="none"/>
      <rect x="30" y="8" width="88" height="106" rx="5" fill="#fff"/>
      <rect x="66" y="78" width="10" height="26"/><rect x="82" y="64" width="10" height="40"/><rect x="98" y="50" width="10" height="54"/>
      <circle cx="82" cy="30" r="10"/><circle cx="82" cy="30" r="3"/>
      <circle cx="42" cy="62" r="22" fill="#fff"/><line x1="26" y1="78" x2="8" y2="96" stroke-width="7"/>
    </svg>
    <h3>Evaluation</h3>
  </div>

  <div class="svc" style="left:60px;top:520px">
    <svg width="124" height="124" viewBox="0 0 124 124" fill="none" stroke="#0094D4" stroke-width="4" stroke-linejoin="round">
      <circle cx="68" cy="62" r="42" fill="#FBE8D2" stroke="none"/>
      <path d="M22 62a40 40 0 0 1 66-30M102 62a40 40 0 0 1-66 30"/>
      <path d="M84 24l6 8-9 4M40 100l-6-8 9-4"/>
      <path d="M40 96c0-18 10-26 22-26s22 8 22 26"/>
      <path d="M44 58a18 18 0 0 1 36 0"/><rect x="38" y="56" width="8" height="14" rx="3"/><rect x="78" y="56" width="8" height="14" rx="3"/>
      <rect x="86" y="6" width="30" height="20" rx="4" fill="#fff"/><line x1="92" y1="14" x2="110" y2="14"/>
    </svg>
    <h3>Pilot &amp; Emerging<br>Tech Support</h3>
  </div>
  <div class="svc" style="left:420px;top:520px">
    <svg width="124" height="124" viewBox="0 0 124 124" fill="none" stroke="#0094D4" stroke-width="4" stroke-linejoin="round">
      <circle cx="76" cy="56" r="42" fill="#FBE8D2" stroke="none"/>
      <rect x="6" y="6" width="84" height="64" rx="4" fill="#fff"/>
      <line x1="16" y1="22" x2="52" y2="22"/><line x1="16" y1="34" x2="44" y2="34"/>
      <circle cx="98" cy="18" r="10"/>
      <rect x="26" y="56" width="90" height="60" rx="6" fill="#fff"/>
      <path d="M56 56v-10h30v10M26 80h90"/><rect x="64" y="74" width="14" height="12" fill="#fff"/>
    </svg>
    <h3>Program Portfolio<br>&amp; Resource Planning</h3>
  </div>
  <div class="svc" style="left:780px;top:520px">
    <svg width="124" height="124" viewBox="0 0 124 124" fill="none" stroke="#0094D4" stroke-width="4" stroke-linejoin="round">
      <circle cx="72" cy="60" r="42" fill="#FBE8D2" stroke="none"/>
      <path d="M30 62a24 24 0 0 1 48 0"/><rect x="24" y="58" width="10" height="18" rx="3"/><rect x="74" y="58" width="10" height="18" rx="3"/>
      <path d="M84 74c0 8-8 10-18 10"/>
      <rect x="18" y="90" width="72" height="28" rx="5" fill="#fff"/>
      <rect x="78" y="8" width="38" height="26" rx="4" fill="#fff"/><line x1="86" y1="18" x2="108" y2="18"/><line x1="86" y1="26" x2="100" y2="26"/>
    </svg>
    <h3>Program Delivery<br>Support</h3>
  </div>
</section>

<section class="overview">
  <div class="backing"></div>
  <div class="photo" role="img" aria-label="Person at a desktop computer viewing an analytics dashboard"></div>
  <h2 class="heading" style="color:var(--white)">Company Overview</h2>
  <p>Harrow Point Metrics (HPM) was formed in 2016 to help utilities and regulatory agencies navigate the technical, economic, and policy challenges of building a smarter and cleaner energy future. Our research focuses on impact analysis as well as predictive and causal analytics. We deliver data-driven insights into how various technologies and interventions affect the way homes and businesses use energy and how those in turn affect grid and system planning.</p>
  <a class="btn">Read More</a>
</section>

<section class="cases">
  <div class="frame"></div>
  <div class="backing"></div>
  <div class="photo" role="img" aria-label="Analyst working on a tablet surrounded by holographic data charts"></div>
  <h2 class="heading">Proposed Case Studies<br>for Each Core Service</h2>
  <ul class="checklist">
    <li>Predictive Analytics and Forecasting</li>
    <li>T&amp; D Planning – NVPG or Central Brookfield?</li>
    <li>Evaluation – CLE? MVG&amp;E? Different state?</li>
    <li>Pilot &amp; Emerging Tech Support – Ag DR Study?<br>TVP&amp;E Battery Pilot?</li>
    <li>Program Portfolio &amp; Resource Planning – PA Work?</li>
    <li>Program Delivery Support – CERP?</li>
  </ul>
</section>

<section class="research">
  <h2 class="heading">Research and Analysis</h2>
  <svg class="arrow" style="left:34px" width="22" height="36" viewBox="0 0 22 36" fill="none" stroke="#555" stroke-width="2.5"><polyline points="19,2 3,18 19,34"/></svg>
  <svg class="arrow" style="left:1148px" width="22" height="36" viewBox="0 0 22 36" fill="none" stroke="#555" stroke-width="2.5"><polyline points="3,2 19,18 3,34"/></svg>

  <article class="card" style="left:74px">
    <div class="photo" role="img" aria-label="Team meeting in front of a wall screen showing charts" style="background:linear-gradient(135deg,#9fb0c0,#2d4f72)"></div>
    <h3>Duis aute irure dolor</h3>
    <p>Nemo enim ipsam voluptatem quia voluptas sit aspernatur aut odit aut fugit, sed quia consequuntur magni.</p>
    <a>Read More</a>
  </article>
  <article class="card" style="left:436px">
    <div class="photo" role="img" aria-label="Presenter beside a screen of bar charts in a meeting room" style="background:linear-gradient(135deg,#dfe5ea,#7f9bb5)"></div>
    <h3>Duis aute irure dolor</h3>
    <p>Nemo enim ipsam voluptatem quia voluptas sit aspernatur aut odit aut fugit, sed quia consequuntur magni.</p>
    <a>Read More</a>
  </article>
  <article class="card" style="left:798px">
    <div class="photo" role="img" aria-label="Analyst at a laptop reviewing printed reports and charts" style="background:linear-gradient(135deg,#3f4a55,#a7b6c4)"></div>
    <h3>Duis aute irure dolor</h3>
    <p>Nemo enim ipsam voluptatem quia voluptas sit aspernatur aut odit aut fugit, sed quia consequuntur magni.</p>
    <a>Read More</a>
  </article>

  <a class="btn">Read All Case Studies</a>
</section>

<footer class="site-footer">
  <div class="brand"><span class="brand-dot"></span><span class="brand-name">Harrow Point Metrics</span></div>
  <div class="copyright">Copyright ©2022 by Company Name<br>All Right Reserved</div>

  <div class="foot-head" style="left:376px">Site Map</div>
  <div class="foot-links" style="left:376px;top:92px">Home<br>About Us<br>Core Services</div>
  <div class="foot-links" style="left:511px;top:92px">Our Work<br>Blog<br>Contact Us</div>

  <div class="foot-head" style="left:650px">Contact Us</div>
  <div class="contact">
    <div class="co">Harrow Point Metrics</div>
    <div>418 Linden Crest<br>Ave NE Suite B2 Marlow,<br>GA 30999</div>
    <div class="row">
      <svg width="12" height="14" viewBox="0 0 12 14" fill="none" stroke="#F0912C" stroke-width="2"><path d="M3 1c-2 1-2 4 0 7s5 5 7 4l1-2-3-2-1 1c-1-1-2-2-3-4l1-1-1-3z"/></svg>
      <span>555.010.4821</span>
    </div>
    <div class="row">
      <svg width="13" height="10" viewBox="0 0 13 10"><rect width="13" height="10" rx="1" fill="#F0912C"/><polyline points="1,1 6.5,6 12,1" fill="none" stroke="#fff" stroke-width="1.2"/></svg>
      <span>hello@harrowpointmetrics.example</span>
    </div>
  </div>

  <div class="foot-head" style="left:946px">Follow Us</div>
  <div class="social" aria-label="Social links"><span></span><span></span><span></span><span></span></div>
</footer>

</body>
</html>
```